Trading Company needs a business card design, letter head design and email signature

We need a double-sided business card design, letter head design and an email signature. We have a logo design.

Possible Tag Lines:
• “Connecting Worlds, Building Excellence.”
• “Global Sourcing, Local Excellence.”
• “Bridging Borders, Building Quality.”
• “Worldwide Partnerships, Superior Goods.”
• “Where Quality Meets Affordability”

Services Offered:
Procurement
Fabrication
Distribution
Logistics
Import/Export

Requirements
Must have
• Nice quality double sided Business Card design, Letterhead design needs to be A4
Nice to have
• possible ideas on tag lines

```html
<!DOCTYPE html>
<html lang="en">
<head>
<meta charset="utf-8">
<title>Norvane Business Card</title>
<link href="https://fonts.googleapis.com/css2?family=Open+Sans:wght@400;600;700&display=swap" rel="stylesheet">
<style>
  :root {
    --canvas-bg: #242424;
    --card-dark: #1f1f23;
    --card-grey: #55585a;
    --brand-red: #e3202a;
    --text-white: #ffffff;
    --text-grey: #5d6063;
    --text-soft: #e9e9e9;
    --emboss: #3f4244;
  }
  * { box-sizing: border-box; margin: 0; padding: 0; }
  html, body {
    width: 1200px; height: 775px; overflow: hidden;
    background: var(--canvas-bg);
    font-family: "Open Sans", sans-serif;
  }
  .sheet {
    position: relative; width: 1200px; height: 775px;
    display: flex; align-items: center; justify-content: center; gap: 40px;
  }
  .card {
    position: relative; width: 540px; height: 310px;
    border-radius: 22px; overflow: hidden;
    box-shadow: 0 14px 30px rgba(0,0,0,.45);
  }

  /* Front */
  .card-front { background: var(--card-dark); }
  .holder { position: absolute; left: 34px; top: 40px; }
  .holder-name { font-size: 34px; font-weight: 600; line-height: 1.1; color: var(--brand-red); }
  .holder-name .surname { color: var(--text-grey); }
  .holder-title { margin-top: 4px; font-size: 17px; color: var(--text-white); }
  .divider { position: absolute; left: 228px; top: 120px; }
  .brand-front { position: absolute; right: 36px; top: 44px; display: flex; align-items: center; gap: 12px; }
  .brand-word { font-size: 30px; font-weight: 700; letter-spacing: 3px; color: var(--brand-red); }
  .brand-square { width: 26px; height: 26px; background: var(--brand-red); }
  .contacts { position: absolute; left: 300px; top: 128px; list-style: none; }
  .contacts li { display: flex; align-items: center; gap: 10px; font-size: 16px; color: var(--text-white); line-height: 27px; }
  .contacts svg { width: 15px; height: 15px; fill: var(--brand-red); flex: none; }
  .services-label {
    position: absolute; left: 34px; top: 228px;
    font-size: 14px; font-weight: 700; color: var(--brand-red); letter-spacing: .5px;
  }
  .services-band {
    position: absolute; left: 0; right: 0; bottom: 0; height: 38px;
    background: var(--brand-red);
    display: flex; align-items: center; justify-content: space-between;
    padding: 0 24px;
    list-style: none;
  }
  .services-band li { display: flex; align-items: center; gap: 7px; font-size: 13.5px; color: var(--text-white); white-space: nowrap; }
  .services-band li::before { content: ""; width: 6px; height: 6px; background: var(--text-white); transform: rotate(45deg); }

  /* Back */
  .card-back { background: var(--card-grey); }
  .brand-back {
    position: absolute; left: 0; right: 0; top: 92px;
    display: flex; align-items: center; justify-content: center; gap: 16px;
  }
  .brand-back .brand-word { font-size: 44px; letter-spacing: 5px; color: var(--emboss); }
  .brand-back .brand-square { width: 40px; height: 40px; background: var(--emboss); }
  .taglines {
    position: absolute; left: 24px; right: 20px; bottom: 34px;
    list-style: none; display: flex; flex-wrap: wrap; column-gap: 12px; row-gap: 6px;
  }
  .taglines li { display: flex; align-items: center; gap: 6px; font-size: 11.5px; color: var(--text-soft); }
  .taglines li::before { content: ""; width: 6px; height: 6px; border: 1px solid var(--text-soft); transform: rotate(45deg); }
</style>
</head>
<body>
<main class="sheet">
  <section class="card card-front">
    <div class="holder">
      <h1 class="holder-name">Daniel <span class="surname">Ravik</span></h1>
      <p class="holder-title">Managing Director</p>
    </div>
    <svg class="divider" width="60" height="100" viewBox="0 0 60 100"><line x1="58" y1="2" x2="2" y2="98" stroke="var(--brand-red)" stroke-width="1"/></svg>
    <div class="brand-front">
      <span class="brand-word">NORVANE</span>
      <span class="brand-square"></span>
    </div>
    <ul class="contacts">
      <li><svg viewBox="0 0 24 24"><path d="M6.6 10.8a15 15 0 006.6 6.6l2.2-2.2c.3-.3.7-.4 1-.2 1.1.4 2.3.6 3.6.6.6 0 1 .4 1 1V20c0 .6-.4 1-1 1A17 17 0 013 4c0-.6.4-1 1-1h3.5c.6 0 1 .4 1 1 0 1.3.2 2.5.6 3.6.1.3 0 .7-.2 1z"/></svg>(555) 014-2870</li>
      <li><svg viewBox="0 0 24 24"><path d="M2 5h20v14H2zm2 2v.5l8 5 8-5V7l-8 5z"/></svg>info@norvanetrade.com</li>
      <li><svg viewBox="0 0 24 24"><path d="M12 2a10 10 0 100 20 10 10 0 000-20zm0 2c1 1.2 1.8 3 2.2 5H9.8C10.2 7 11 5.2 12 4zM4.3 13a8 8 0 010-2h3.4a17 17 0 000 2zm5.5 0a15 15 0 010-2h4.4a15 15 0 010 2zm6.5 0a17 17 0 000-2h3.4a8 8 0 010 2zM12 20c-1-1.2-1.8-3-2.2-5h4.4c-.4 2-1.2 3.8-2.2 5z"/></svg>www.norvanetrade.com</li>
    </ul>
    <p class="services-label">SERVICES</p>
    <ul class="services-band">
      <li>Procurement</li>
      <li>Fabrication</li>
      <li>Distribution</li>
      <li>Logistics</li>
      <li>Import/Export</li>
    </ul>
  </section>

  <section class="card card-back">
    <div class="brand-back">
      <span class="brand-word">NORVANE</span>
      <span class="brand-square"></span>
    </div>
    <ul class="taglines">
      <li>Connecting Worlds, Building Excellence</li>
      <li>Global Sourcing, Local Excellence</li>
      <li>Bridging Borders, Building Quality</li>
      <li>Worldwide Partnerships, Superior Goods</li>
      <li>Where Quality Meets Affordability</li>
    </ul>
  </section>
</main>
</body>
</html>
```